Construction company business card

One side to be the logo with the company name, The other side I would like: (Tomas verbick) Project manager 41 barrow crescent hallam 52917306224783(03) 9703 2428Info@gudeljgroup.comAnd then maybe a couple dot points saying what we do:Construction (commercial & industrial) Civil construction

Anything else please contact me!
Maybe curved st one edge of the card

Target Market(s)

Older clientele

Industry/Entity Type

Construction Company

Contact Information for Business Card

Read above

Colors
3277b5
1b1b1b
9d9d9d

Requirements
Must have
• Use my logo on one side
Nice to have
• Read above
Should not have
• Read above

```html
<!DOCTYPE html>
<html lang="en">
<head>
<meta charset="utf-8">
<title>Stonebay Construction – Business Card</title>
<link rel="stylesheet" href="https://fonts.googleapis.com/css2?family=Work+Sans:wght@400;500;600&display=swap">
<style>
  :root {
    --bg: #161616;
    --card: #1b1b1b;
    --card-edge: #222222;
    --silver: #d4d4d4;
    --silver-soft: #9d9d9d;
    --emboss: #101010;
    --emboss-light: #333333;
    --accent: #3277b5;
  }
  * { margin: 0; padding: 0; box-sizing: border-box; }
  html, body {
    width: 1200px; height: 900px; overflow: hidden;
    background: radial-gradient(ellipse at 60% 40%, #262626 0%, var(--bg) 70%);
    font-family: "Work Sans", sans-serif;
  }
  .canvas { position: relative; width: 1200px; height: 900px; }
  .card {
    position: absolute; left: 280px; width: 640px; height: 366px;
    background: linear-gradient(135deg, var(--card) 0%, #202020 60%, #1c1c1c 100%);
    border: 1px solid var(--card-edge);
    box-shadow: 0 18px 40px rgba(0,0,0,0.6);
  }
  .card--front { top: 64px; }
  .card--back { top: 470px; }

  .brand {
    position: absolute; inset: 0;
    display: flex; align-items: center; justify-content: center; gap: 18px;
  }
  .brand__dot {
    width: 54px; height: 54px; border-radius: 50%;
    border: 4px solid var(--silver);
    flex-shrink: 0;
  }
  .brand__name {
    color: var(--silver); font-weight: 600;
    font-size: 34px; line-height: 1.1; letter-spacing: 2px;
    text-transform: uppercase;
  }
  .brand__name span { display: block; font-size: 15px; letter-spacing: 7.4px; }

  .person {
    position: absolute; left: 70px; top: 122px; text-align: right; width: 220px;
  }
  .person__name {
    font-size: 21px; font-weight: 500; letter-spacing: 1px; text-transform: uppercase;
    color: var(--emboss); text-shadow: 0 1px 0 var(--emboss-light);
    white-space: nowrap;
  }
  .person__role {
    font-size: 17px; color: var(--emboss); text-shadow: 0 1px 0 var(--emboss-light);
    margin-top: 2px;
  }
  .divider {
    position: absolute; left: 316px; top: 118px; width: 1px; height: 72px;
    background: var(--silver-soft); opacity: 0.7;
  }
  .contact {
    position: absolute; left: 340px; top: 118px; list-style: none;
    color: var(--silver); font-size: 17px; letter-spacing: 0.5px;
  }
  .contact li { display: flex; align-items: center; gap: 10px; height: 25px; white-space: nowrap; }
  .contact svg { width: 13px; height: 13px; fill: none; stroke: var(--silver); stroke-width: 1.6; flex-shrink: 0; }
  .address {
    position: absolute; left: 0; right: 0; bottom: 44px; text-align: center;
    font-size: 17px; letter-spacing: 1px;
    color: var(--emboss); text-shadow: 0 1px 0 var(--emboss-light);
    white-space: nowrap;
  }
  .address span { color: var(--silver); text-shadow: none; }
</style>
</head>
<body>
<main class="canvas">
  <section class="card card--front">
    <div class="brand">
      <div class="brand__dot"></div>
      <div class="brand__name">Stonebay<span>Construction</span></div>
    </div>
  </section>

  <section class="card card--back">
    <div class="person">
      <div class="person__name">Tomas Verbick</div>
      <div class="person__role">Project manager</div>
    </div>
    <div class="divider"></div>
    <ul class="contact">
      <li>
        <svg viewBox="0 0 16 16"><path d="M4 2l2.5 3-1.5 1.5a8 8 0 0 0 4.5 4.5L11 9.5l3 2.5-1.5 2C7 14 2 9 2 3.5z"/></svg>
        73 0622 4783
      </li>
      <li>
        <svg viewBox="0 0 16 16"><rect x="4" y="1.5" width="8" height="13" rx="1.5"/><path d="M7 12h2"/></svg>
        (03) 9418 6573
      </li>
      <li>
        <svg viewBox="0 0 16 16"><rect x="1.5" y="3.5" width="13" height="9"/><path d="M1.5 3.5L8 9l6.5-5.5"/></svg>
        Info@verbickgroup.com
      </li>
    </ul>
    <p class="address">41 barrow crescent kestwood <span>5291</span></p>
  </section>
</main>
</body>
</html>
```